Web Developer Needs a Business Card Design

I need a personal business card design that represents me as a web developer for potential employers. I would like the background to be a dark color on the front for contrast with my logo and name. The back will have all my information along with a smaller version of the logo. I want something with a modern look and feel, not too conservative. This will be used for potential employers and freelance work.

Industry/Entity Type

Business

Contact Information for Business Card

Front should have my logo and name. The back should have all my personal information which would include: name: Tom Varulek, phone: 570-614-3098, email: tomvarulek@quillbox.net, website url: www.tomvarulek.net, logo, web developer.

Font styles to use
Sans Serif

Requirements
Must have
• Must include my logo. The color palette base color will be the logo color.

```html
<!DOCTYPE html>
<html lang="en">
<head>
<meta charset="utf-8">
<title>Tom Varulek — Business Card</title>
<link rel="stylesheet" href="https://fonts.googleapis.com/css2?family=Open+Sans:ital,wght@0,400;0,600;0,700;1,600;1,700&display=swap">
<style>
  :root {
    --stage-light: #2a2a2a;
    --stage-dark: #0b0b0b;
    --card-top: #1c1c1c;
    --card-bottom: #050505;
    --teal: #6ec9b4;
    --name-grey: #e4e4e4;
    --text-grey: #c9c9c9;
    --shadow: rgba(0,0,0,.7);
  }
  * { margin: 0; padding: 0; box-sizing: border-box; }
  html, body { width: 1200px; height: 864px; overflow: hidden; }
  body {
    background: radial-gradient(ellipse at 50% 40%, var(--stage-light) 0%, var(--stage-dark) 75%);
    font-family: "Open Sans", sans-serif;
    position: relative;
  }
  .card {
    position: absolute;
    width: 525px;
    height: 300px;
    border-radius: 3px;
    background: linear-gradient(160deg, var(--card-top) 0%, var(--card-bottom) 60%);
    box-shadow: 0 18px 40px var(--shadow);
    overflow: hidden;
  }
  .card--back { left: 600px; top: 150px; }
  .card--front { left: 75px; top: 430px; }

  .brand {
    position: absolute;
    right: 40px;
    bottom: 38px;
    display: flex;
    flex-direction: column;
    align-items: flex-end;
    gap: 14px;
  }
  .brand-mark {
    display: flex;
    align-items: center;
    gap: 8px;
    color: var(--teal);
    font-weight: 600;
    font-size: 15px;
    letter-spacing: .5px;
  }
  .brand-mark .dot {
    width: 40px; height: 40px;
    border-radius: 50%;
    background: var(--teal);
  }
  .brand-name {
    color: var(--name-grey);
    font-size: 27px;
    font-weight: 400;
    letter-spacing: .5px;
  }
  .card--back .brand-name { font-size: 22px; }
  .card--back .brand-mark .dot { width: 34px; height: 34px; }

  .contact {
    position: absolute;
    left: 36px;
    top: 44px;
    font-size: 12px;
    color: var(--text-grey);
  }
  .contact-title {
    font-weight: 700;
    font-style: italic;
    font-size: 13px;
    margin-bottom: 8px;
  }
  .contact-title .person { color: var(--teal); }
  .contact-title .sep { color: var(--text-grey); margin: 0 5px; font-style: normal; }
  .contact-title .role { color: var(--name-grey); }
  .contact-list { list-style: none; }
  .contact-list li {
    display: flex;
    align-items: center;
    gap: 8px;
    height: 19px;
  }
  .contact-list svg { width: 12px; height: 12px; flex: none; }
</style>
</head>
<body>

  <section class="card card--back" aria-label="Card back">
    <div class="contact">
      <p class="contact-title"><span class="person">Tom Varulek</span><span class="sep">|</span><span class="role">Web Developer</span></p>
      <ul class="contact-list">
        <li>
          <svg viewBox="0 0 12 12" aria-hidden="true"><rect width="12" height="12" rx="2" fill="#6ec9b4"/><path d="M3.5 3 L5 3 L5.6 4.8 L4.8 5.4 Q5.6 7 6.8 7.4 L7.4 6.6 L9 7.2 L9 8.6 Q5 9 3.4 4.4 Z" fill="#111"/></svg>
          <span>(570) 614-3098</span>
        </li>
        <li>
          <svg viewBox="0 0 12 12" aria-hidden="true"><rect width="12" height="12" rx="2" fill="#6ec9b4"/><rect x="2.5" y="3.5" width="7" height="5" fill="none" stroke="#111" stroke-width="1"/><path d="M2.5 3.5 L6 6.3 L9.5 3.5" fill="none" stroke="#111" stroke-width="1"/></svg>
          <span>tomvarulek@quillbox.net</span>
        </li>
        <li>
          <svg viewBox="0 0 12 12" aria-hidden="true"><rect width="12" height="12" rx="2" fill="#6ec9b4"/><circle cx="6" cy="6" r="3.5" fill="none" stroke="#111" stroke-width="1"/><path d="M2.5 6 H9.5 M6 2.5 Q4 6 6 9.5 M6 2.5 Q8 6 6 9.5" fill="none" stroke="#111" stroke-width=".8"/></svg>
          <span>www.tomvarulek.net</span>
        </li>
      </ul>
    </div>
    <div class="brand">
      <div class="brand-mark"><span class="dot"></span><span>varulek</span></div>
      <p class="brand-name">TOM VARULEK</p>
    </div>
  </section>

  <section class="card card--front" aria-label="Card front">
    <div class="brand">
      <div class="brand-mark"><span class="dot"></span><span>varulek</span></div>
      <p class="brand-name">TOM VARULEK</p>
    </div>
  </section>

</body>
</html>
```